Road Construction Company needs business cards

We would like a new business card designed for our business.

We're a road construction company based in Qld, Australia.

Can the business card please have the following information on it.

Name: Warren Halbeck
Position: General Manager
Phone: 0472 915 348
Email: Warren.halbeck@tovrin.com.au
Address: 87 Marrow Ave, Pendlebay, QLD, 4023
Website: www.tovrin.com.au

Visually we'd like the card to be professional and simple.

Attached is our logo.

Our website is www.tovrin.com.au

Target Market(s)

Men aged 25-60

Contact Information for Business Card

As listed in project description

Font styles to use
Serif

Requirements
Must have
• Large logo on back of card

```html
<!DOCTYPE html>
<html lang="en">
<head>
<meta charset="utf-8">
<title>Tovrin Business Card</title>
<link rel="stylesheet" href="https://fonts.googleapis.com/css2?family=Lato:wght@400;700;900&display=swap">
<style>
  :root {
    --stage: #2a2a2c;
    --brand-blue: #0455a6;
    --brand-navy: #0b3f8f;
    --accent-sky: #2fa6e0;
    --paper: #ffffff;
    --ink: #1f1f1f;
    --rule: #4a86c8;
  }
  * { margin: 0; padding: 0; box-sizing: border-box; }
  html, body { width: 1200px; height: 875px; overflow: hidden; }
  body {
    background: var(--stage);
    font-family: "Lato", sans-serif;
    display: flex;
    flex-direction: column;
    align-items: center;
    justify-content: center;
    gap: 56px;
  }
  .card {
    position: relative;
    width: 600px;
    height: 343px;
    border-radius: 22px;
    overflow: hidden;
  }
  .card__band {
    position: absolute;
    left: 0; right: 0; bottom: 0;
    height: 16px;
  }

  /* back */
  .card--back { background: var(--brand-blue); }
  .card--back .card__band { background: var(--accent-sky); }
  .back__brand {
    position: absolute;
    inset: 0 0 16px 0;
    display: flex;
    align-items: center;
    justify-content: center;
    gap: 18px;
  }
  .brand-mark {
    width: 26px; height: 26px;
    background: var(--accent-sky);
  }
  .back__name {
    font-weight: 900;
    font-size: 84px;
    letter-spacing: 4px;
    color: var(--accent-sky);
  }

  /* front */
  .card--front { background: var(--paper); }
  .card--front .card__band { background: var(--brand-blue); height: 18px; }
  .front__brand {
    position: absolute;
    left: 42px; top: 0; bottom: 18px;
    width: 230px;
    display: flex;
    align-items: center;
    gap: 12px;
  }
  .front__brand .brand-mark { width: 18px; height: 18px; background: var(--brand-navy); }
  .front__name {
    font-weight: 900;
    font-size: 48px;
    letter-spacing: 2px;
    color: var(--brand-navy);
  }
  .front__rule {
    position: absolute;
    left: 292px; top: 56px;
    width: 1px; height: 210px;
    background: var(--rule);
  }
  .contact {
    position: absolute;
    left: 318px; top: 64px;
    right: 24px;
  }
  .contact__person {
    font-weight: 900;
    font-size: 27px;
    color: var(--brand-navy);
    text-transform: uppercase;
    letter-spacing: 0.3px;
    line-height: 1;
  }
  .contact__role {
    font-size: 17px;
    color: var(--accent-sky);
    margin-top: 4px;
    margin-bottom: 16px;
  }
  .contact__row {
    display: flex;
    align-items: flex-start;
    gap: 10px;
    font-size: 15px;
    color: var(--ink);
    line-height: 1.35;
    margin-bottom: 6px;
  }
  .contact__row svg { flex: none; width: 14px; height: 14px; margin-top: 3px; fill: var(--brand-blue); }
  .contact__row--spaced { margin-bottom: 14px; }
</style>
</head>
<body>

  <section class="card card--back" aria-label="Card back">
    <div class="back__brand">
      <span class="brand-mark"></span>
      <span class="back__name">TOVRIN</span>
    </div>
    <div class="card__band"></div>
  </section>

  <section class="card card--front" aria-label="Card front">
    <div class="front__brand">
      <span class="brand-mark"></span>
      <span class="front__name">TOVRIN</span>
    </div>
    <div class="front__rule"></div>
    <div class="contact">
      <p class="contact__person">Warren Halbeck</p>
      <p class="contact__role">General Manager</p>
      <div class="contact__row contact__row--spaced">
        <svg viewBox="0 0 24 24" aria-hidden="true"><path d="M12 2a7 7 0 0 0-7 7c0 5 7 13 7 13s7-8 7-13a7 7 0 0 0-7-7zm0 9.5A2.5 2.5 0 1 1 12 6.5a2.5 2.5 0 0 1 0 5z"/></svg>
        <span>87 Marrow Ave,<br>Pendlebay, QLD, 4023</span>
      </div>
      <div class="contact__row">
        <svg viewBox="0 0 24 24" aria-hidden="true"><path d="M6.6 10.8a15 15 0 0 0 6.6 6.6l2.2-2.2a1 1 0 0 1 1-.25 11.4 11.4 0 0 0 3.6.57 1 1 0 0 1 1 1V20a1 1 0 0 1-1 1A17 17 0 0 1 3 4a1 1 0 0 1 1-1h3.5a1 1 0 0 1 1 1c0 1.25.2 2.45.57 3.6a1 1 0 0 1-.25 1z"/></svg>
        <span>0472 915 348</span>
      </div>
      <div class="contact__row">
        <svg viewBox="0 0 24 24" aria-hidden="true"><path d="M2 5h20v14H2zm2 2v.5l8 5 8-5V7l-8 5z"/></svg>
        <span>Warren.halbeck@tovrin.com.au</span>
      </div>
      <div class="contact__row">
        <svg viewBox="0 0 24 24" aria-hidden="true"><path d="M12 2a10 10 0 1 0 0 20 10 10 0 0 0 0-20zm6.9 9h-3a15 15 0 0 0-1.3-5.6A8 8 0 0 1 18.9 11zM12 4.1c.9 1.3 1.7 3.6 1.9 6.9h-3.8c.2-3.3 1-5.6 1.9-6.9zM9.4 5.4A15 15 0 0 0 8.1 11h-3a8 8 0 0 1 4.3-5.6zM5.1 13h3a15 15 0 0 0 1.3 5.6A8 8 0 0 1 5.1 13zm6.9 6.9c-.9-1.3-1.7-3.6-1.9-6.9h3.8c-.2 3.3-1 5.6-1.9 6.9zm2.6-1.3a15 15 0 0 0 1.3-5.6h3a8 8 0 0 1-4.3 5.6z"/></svg>
        <span>www.tovrin.com.au</span>
      </div>
    </div>
    <div class="card__band"></div>
  </section>

</body>
</html>
```